Business Card for Industrial Distributor

We need a business card design for an industrial distributor. We sell machine parts for the manufacturing and oil industry. We would like the cards to look clean and modern but with a touch of industry.

Our colors are blue/white.

Please feel free to visit our website www.korvelpartsco.com

Target Market(s)

mexican manufacturers in the automobile/aerospace industry

Industry/Entity Type

Industrial

Colors
ffffff
0555a3

```html
<!DOCTYPE html>
<html lang="en">
<head>
<meta charset="utf-8">
<title>Korvel Business Card</title>
<link href="https://fonts.googleapis.com/css2?family=Arimo:wght@400;700&display=swap" rel="stylesheet">
<style>
  :root {
    --brand-blue: #2f4fb8;
    --brand-blue-deep: #0555a3;
    --card-white: #ffffff;
    --paper-grey: #e4e4e4;
    --edge-grey: #c9c9c9;
    --stage: #efefef;
    --icon-tint: #c8cde0;
  }
  html, body {
    margin: 0;
    padding: 0;
    width: 1200px;
    height: 780px;
    overflow: hidden;
    background: var(--stage);
    font-family: "Arimo", Arial, sans-serif;
  }
  .stage {
    position: relative;
    width: 1200px;
    height: 780px;
  }
  .card {
    position: absolute;
    top: 241px;
    width: 520px;
    height: 298px;
    border-radius: 14px;
    overflow: hidden;
    background: var(--card-white);
    box-shadow: 0 6px 18px rgba(0,0,0,0.18);
  }
  .card-front { left: 50px; }
  .card-back { left: 630px; }
  .card-art {
    position: absolute;
    inset: 0;
    width: 520px;
    height: 298px;
  }
  .wordmark {
    position: absolute;
    margin: 0;
    font-weight: 700;
    color: var(--brand-blue);
    letter-spacing: -1px;
    line-height: 1;
  }
  .card-front .wordmark {
    left: 34px;
    top: 70px;
    font-size: 68px;
  }
  .card-back .wordmark {
    left: 236px;
    top: 112px;
    font-size: 62px;
  }
  .holder {
    position: absolute;
    left: 214px;
    top: 232px;
    color: var(--card-white);
    font-size: 12px;
    line-height: 1.3;
  }
  .holder-name {
    margin: 0 0 3px;
    font-weight: 700;
    font-size: 14px;
    letter-spacing: 0.5px;
  }
  .holder-address { margin: 0; }
  .divider {
    position: absolute;
    left: 340px;
    top: 176px;
    width: 1px;
    height: 92px;
    background: rgba(255,255,255,0.6);
  }
  .contact-list {
    position: absolute;
    left: 352px;
    top: 176px;
    margin: 0;
    padding: 0;
    list-style: none;
    color: var(--card-white);
    font-size: 12px;
  }
  .contact-list li {
    display: flex;
    align-items: center;
    gap: 7px;
    height: 23px;
  }
  .contact-icon {
    width: 14px;
    height: 14px;
    flex: none;
  }
  .web-address {
    position: absolute;
    left: 40px;
    top: 246px;
    margin: 0;
    color: var(--card-white);
    font-size: 12px;
  }
</style>
</head>
<body>
<main class="stage">

  <section class="card card-front" aria-label="Card front">
    <svg class="card-art" viewBox="0 0 520 298" aria-hidden="true">
      <path d="M0 298 L0 252 Q 290 244 414 0 L520 0 L520 298 Z" fill="var(--edge-grey)"/>
      <path d="M0 298 L0 258 Q 296 249 422 0 L520 0 L520 298 Z" fill="var(--paper-grey)"/>
      <path d="M0 298 L0 264 Q 302 254 432 0 L520 0 L520 298 Z" fill="var(--brand-blue)"/>
    </svg>
    <h1 class="wordmark">Korvel</h1>
    <div class="holder">
      <p class="holder-name">DANIEL REYES</p>
      <p class="holder-address">4120 Harbor Mill Rd.<br>Riverside, TX 78590</p>
    </div>
    <span class="divider"></span>
    <ul class="contact-list">
      <li>
        <svg class="contact-icon" viewBox="0 0 14 14" aria-hidden="true"><rect width="14" height="14" rx="2" fill="var(--icon-tint)"/><path d="M4 3 L6 3 L6.6 5.5 L5.4 6.3 Q6.4 8.2 7.7 8.6 L8.5 7.4 L11 8 L11 10 Q7.5 11 5 8.5 Q3 6 4 3 Z" fill="var(--brand-blue)"/></svg>
        (555) 214 - 3307
      </li>
      <li>
        <svg class="contact-icon" viewBox="0 0 14 14" aria-hidden="true"><rect width="14" height="14" rx="2" fill="var(--icon-tint)"/><rect x="3" y="5" width="8" height="6" fill="var(--brand-blue)"/><rect x="4.5" y="2.5" width="5" height="3" fill="none" stroke="var(--brand-blue)"/></svg>
        (555) 214 - 3308
      </li>
      <li>
        <svg class="contact-icon" viewBox="0 0 14 14" aria-hidden="true"><rect width="14" height="14" rx="2" fill="var(--icon-tint)"/><rect x="2.5" y="4" width="9" height="6.5" fill="none" stroke="var(--brand-blue)"/><path d="M2.5 4 L7 7.8 L11.5 4" fill="none" stroke="var(--brand-blue)"/></svg>
        sales@korvelpartsco.com
      </li>
      <li>
        <svg class="contact-icon" viewBox="0 0 14 14" aria-hidden="true"><rect width="14" height="14" rx="2" fill="var(--icon-tint)"/><circle cx="7" cy="7" r="4.5" fill="none" stroke="var(--brand-blue)"/><path d="M2.5 7 H11.5 M7 2.5 V11.5" stroke="var(--brand-blue)"/></svg>
        www.korvelpartsco.com
      </li>
    </ul>
  </section>

  <section class="card card-back" aria-label="Card back">
    <svg class="card-art" viewBox="0 0 520 298" aria-hidden="true">
      <path d="M0 0 L100 0 Q 150 236 520 252 L520 298 L0 298 Z" fill="var(--edge-grey)"/>
      <path d="M0 0 L94 0 Q 144 242 520 258 L520 298 L0 298 Z" fill="var(--paper-grey)"/>
      <path d="M0 0 L86 0 Q 136 250 520 266 L520 298 L0 298 Z" fill="var(--brand-blue)"/>
    </svg>
    <h2 class="wordmark">Korvel</h2>
    <p class="web-address">www.korvelpartsco.com</p>
  </section>

</main>
</body>
</html>
```